I want ideas sample designs for my book cover

Hello,

We need a book cover designed in flat and 3D Versions. We would like to have jpg and png for final output and include a copy of the PSD for future revisions.

Here are the basic details:

Title: The Harvest of Quiet Builders
Author: Norman Quillfeather

Dimensions of book:

Was looking at the Pavo website for dimensions. I thought you may want to go on there and look at the different sizes. I used the 6x9” perfect bound US trade size for my book. You will see that this has a spine width of 0.225”, Cover size of 12.48 x 9.25” and spine begins at 6.125”

If you need background info on the author just to get an idea what he does, please check:

http://NormanQuillfeather.example

IMPORTANT: Please see attached document for a more detailed info:

Exact Title Of book
Back Cover
Spine Info
Measurements of book and dimension
Examples of book covers
Norman's photo attached

Thanks,
Darlene

Industry/Entity Type

Life Coaching

Font styles to use
Serif

Requirements
Must have
• Jpg, png and PSD files
• title
• author
• exact dimensions
• front and back cover
• flat and 3d versions

```html
<!DOCTYPE html>
<html lang="en">
<head>
<meta charset="utf-8">
<title>The Harvest of Quiet Builders – Cover Spread</title>
<link href="https://fonts.googleapis.com/css2?family=Oswald:wght@700&family=Source+Sans+3:ital,wght@0,400;0,600;0,700;1,400&display=swap" rel="stylesheet">
<style>
  :root {
    --back-blue: #11508f;
    --lime: #cbdd83;
    --ink: #ffffff;
    --spine-ink: #163f6e;
    --night: #0b1730;
    --dusk: #5a6f93;
  }
  * { margin: 0; padding: 0; box-sizing: border-box; }
  html, body { width: 1200px; height: 893px; overflow: hidden; background: #fff; }
  .cover {
    position: relative; width: 1200px; height: 893px; overflow: hidden;
    font-family: "Source Sans 3", "Myriad Pro", sans-serif; color: var(--ink);
  }
  .back-cover {
    position: absolute; left: 0; top: 0; width: 614px; height: 893px;
    background: var(--back-blue);
  }
  .blurb {
    position: absolute; left: 50px; top: 50px; width: 504px;
    font-size: 12.4px; line-height: 16.8px; text-align: justify; hyphens: auto;
  }
  .blurb p + p { margin-top: 16.5px; }
  .author-photo-frame {
    position: absolute; left: 50px; top: 590px; width: 164px; height: 164px;
    background: var(--lime); padding: 6px;
  }
  .author-photo {
    width: 100%; height: 100%;
    background: linear-gradient(135deg, #e6e6e6, #9a9a9a 60%, #cfcfcf);
  }
  .author-bio {
    position: absolute; left: 227px; top: 589px; width: 327px;
    font-size: 11.3px; line-height: 14.5px; text-align: justify; hyphens: auto;
  }
  .website {
    position: absolute; left: 72px; top: 805px;
    font-size: 11.5px; font-style: italic;
  }
  .isbn-box {
    position: absolute; left: 334px; top: 772px; width: 145px; height: 70px;
    background: #fff; color: #000; font-size: 7.5px; text-align: center; padding-top: 6px;
  }
  .spine-band {
    position: absolute; left: 592px; top: 0; width: 22px; height: 596px;
    background: var(--lime);
  }
  .spine-title {
    position: absolute; left: 592px; top: 68px; width: 22px;
    writing-mode: vertical-rl; font-size: 12px; font-weight: 600;
    letter-spacing: 2.1px; color: var(--spine-ink); line-height: 22px;
  }
  .spine-author {
    position: absolute; left: 592px; top: 760px; width: 22px;
    writing-mode: vertical-rl; font-size: 12.5px; line-height: 22px; color: var(--ink);
  }
  .front-cover {
    position: absolute; left: 614px; top: 0; width: 586px; height: 893px;
  }
  .front-photo {
    position: absolute; inset: 0;
    background:
      radial-gradient(ellipse 60% 40% at 55% 30%, #7f93b6 0%, rgba(90,111,147,0) 70%),
      linear-gradient(180deg, #18284b 0%, var(--dusk) 40%, #3a4d70 55%, #1b2a47 75%, var(--night) 100%);
  }
  .series-line {
    position: absolute; left: 0; width: 586px; top: 31px; text-align: center;
    color: var(--lime); font-size: 20px; padding-left: 66px;
  }
  .series-line strong { font-weight: 700; }
  .author-name {
    position: absolute; left: 0; width: 586px; top: 68px; text-align: center;
    font-size: 38px; font-weight: 700; padding-left: 54px;
  }
  .tagline {
    position: absolute; left: 322px; width: 250px; top: 263px; text-align: center;
    font-size: 20.5px; line-height: 24.8px;
  }
  .title-art { position: absolute; left: 48px; top: 556px; }
  .title-art text { font-family: "Oswald", "Impact", sans-serif; font-weight: 700; fill: var(--lime); }
</style>
</head>
<body>
<div class="cover">
  <section class="back-cover">
    <div class="blurb">
      <p>This path goes way beyond Entrepreneurism! This is a book for the awakening Entrepreneurs who are building businesses for a better world, affecting generations to come. Bringing you disruptive (in a good way) information, to turn you and your business inside-out for maximum acceleration towards your organisational vision, mission and values.</p>
      <p>There is the potential to have a more meaningful life and business by discovering the symbiotic relationship that exists between all beings. You will be empowered to take your life and business to the next level if you answer the call in this book. It will introduce you to the power of Amazonian plant medicine and other entheogens for improving relationships with yourself, your partner and your family, friends, business associates and Mother Earth.</p>
      <p>An entheogen is defined as ‘a substance (usually from a plant, but not always) that is consumed in order to alter one’s state of consciousness or to act as a catalyst towards encounters with other states of being.’ Plant medicine has been successfully used in South America for thousands of years. This ancient wisdom is helping billionaires, industry icons and entrepreneurs to be better leaders, awakening to its potential for allowing deep examination of the psyche which has the ability to heal, eliminate fears and create a new level of success both personally and professionally.</p>
      <p>Norman shares his own heart-felt personal experiences and insights gained from working with these substances and the amazing medicine men and women of the Amazon who retain thousands of years of ancient wisdom. He has spent years turning himself inside-out to powerfully transform his own life and business and wants to encourage entrepreneurs to do the same. He believes that if enough people have the opportunity to explore their own consciousness, then together we can make a positive impact on humanity. If you are ready to travel to the fringes and take a journey within, you will discover that you are the missing link you have been looking for. Get ready to expand your consciousness, transform your business and create a new inspiring lifestyle, which will benefit all beings and our beautiful Mother Earth.</p>
    </div>
    <div class="author-photo-frame">
      <div class="author-photo" role="img" aria-label="Black and white portrait photo of the author"></div>
    </div>
    <p class="author-bio">Norman Quillfeather is an internationally-renowned entrepreneur, speaker, philanthropist, thought leader and best-selling author. Having played the role of transformational coach, facilitator and spoken to over three million people from twelve different countries, he challenges you in his second book to journey deep within yourself to examine the core of your true nature and how it impacts your entrepreneurial journey. Some of the world biggest game changers, social entrepreneurs, internet marketers and consultants have reported that Norman’s golden edge is to integrate “purpose with profits” in a way that brings greater meaning to the work they are doing here in the world.</p>
    <p class="website">www.NormanQuillfeather.example</p>
    <div class="isbn-box">ISBN</div>
  </section>

  <div class="spine-band"></div>
  <div class="spine-title">The HARVEST OF QUIET BUILDERS</div>
  <div class="spine-author">Norman Quillfeather</div>

  <section class="front-cover">
    <div class="front-photo" role="img" aria-label="Photograph of a man in a dark suit seen from behind, looking out over the sea at dusk"></div>
    <p class="series-line">From the Best Selling Author of “<strong>Tidewater</strong>”</p>
    <h2 class="author-name">Norman Quillfeather</h2>
    <p class="tagline">How this ancient wisdom is helping billionaires, industry icons and entrepreneurs to be better leaders, increase impact and leave a legacy</p>
    <svg class="title-art" width="500" height="200" viewBox="0 0 500 200" aria-label="The Harvest of Quiet Builders">
      <text x="0" y="84" font-size="54" textLength="60" lengthAdjust="spacingAndGlyphs">The</text>
      <text x="68" y="84" font-size="92" textLength="420" lengthAdjust="spacingAndGlyphs">HARVEST OF</text>
      <text x="14" y="190" font-size="92" textLength="474" lengthAdjust="spacingAndGlyphs">QUIET BUILDERS</text>
    </svg>
  </section>
</div>
</body>
</html>
```